Business Card Design

I need business cards designed for a new company i have started that makes cakes, particularly themed kids cakes with a really modern design and I would like to have my business cards reflect this. I have attached some photos of cakes I have made and would like some to be used.

Industry/Entity Type

Business

Contact Information for Business Card

Business Name: Tarts and Treats by Maren
Mobile: 0492 815 063
email: maren@tartsandtreatsbymaren.example.au
Instagram: instagram.com/tartsandtreatsbymaren/
Facebook: fb.me/tartsandtreatsbymaren

Colors
e667a6
b768aa
3276b5

Requirements
Must have
• Business Name: Tarts and Treats by Maren
• Mobile: 0492 815 063
• email: maren@tartsandtreatsbymaren.example.au
• Instagram: instagram.com/tartsandtreatsbymaren/
• Facebook: fb.me/tartsandtreatsbymaren
Nice to have
• 2 to 3 pictures of my cakes

```html
<!DOCTYPE html>
<html lang="en">
<head>
<meta charset="utf-8">
<title>Tarts and Treats by Maren – Business Card</title>
<link rel="stylesheet" href="https://fonts.googleapis.com/css2?family=Montserrat:wght@400;600;700&display=swap">
<style>
  :root {
    --pink: #e667a6;
    --purple: #b768aa;
    --blue: #3276b5;
    --white: #ffffff;
    --backdrop: #ece8e3;
    --shadow: rgba(40, 30, 20, 0.25);
  }
  * { box-sizing: border-box; margin: 0; padding: 0; }
  html, body { width: 1200px; height: 950px; overflow: hidden; }
  body {
    background: var(--backdrop);
    font-family: "Montserrat", sans-serif;
    position: relative;
  }
  .card {
    position: absolute;
    width: 700px;
    height: 400px;
    border-radius: 4px;
    overflow: hidden;
    box-shadow: 0 12px 30px var(--shadow);
  }
  .card-front { left: 150px; top: 60px; background: var(--blue); }
  .card-back { left: 350px; top: 490px; background: var(--white); }

  .wordmark {
    position: absolute;
    display: flex;
    flex-direction: column;
    align-items: center;
  }
  .wordmark-row { display: flex; align-items: center; gap: 14px; }
  .wordmark-square { width: 22px; height: 22px; }
  .wordmark-name {
    font-weight: 600;
    font-size: 34px;
    letter-spacing: 0.5px;
    white-space: nowrap;
  }
  .wordmark-rule { width: 100%; height: 2px; margin-top: 10px; }

  .card-front .wordmark { left: 50%; top: 50%; transform: translate(-50%, -50%); color: var(--white); }
  .card-front .wordmark-square { background: var(--white); }
  .card-front .wordmark-rule { background: var(--white); opacity: 0.8; }

  .card-back .wordmark { right: 40px; top: 70px; color: var(--pink); }
  .card-back .wordmark-name { font-size: 26px; }
  .card-back .wordmark-square { background: var(--purple); width: 18px; height: 18px; }
  .card-back .wordmark-rule { background: var(--pink); opacity: 0.6; }

  .back-waves { position: absolute; inset: 0; width: 100%; height: 100%; }

  .contact {
    position: absolute;
    left: 44px;
    top: 215px;
    color: var(--white);
  }
  .contact-name { font-weight: 700; font-size: 19px; letter-spacing: 0.5px; text-transform: uppercase; }
  .contact-role { font-size: 13px; margin-top: 2px; margin-bottom: 12px; }
  .contact-list { list-style: none; }
  .contact-item {
    display: flex;
    align-items: center;
    gap: 10px;
    font-size: 13px;
    line-height: 24px;
  }
  .contact-icon { width: 14px; height: 14px; flex: none; }
</style>
</head>
<body>

  <section class="card card-front" aria-label="Card front">
    <div class="wordmark">
      <div class="wordmark-row">
        <span class="wordmark-square"></span>
        <span class="wordmark-name">Tarts and Treats by Maren</span>
      </div>
      <span class="wordmark-rule"></span>
    </div>
  </section>

  <section class="card card-back" aria-label="Card back">
    <svg class="back-waves" viewBox="0 0 700 400" preserveAspectRatio="none" aria-hidden="true">
      <path d="M0 150 C120 130 260 195 360 262 C450 322 560 318 700 292 L700 400 L0 400 Z" fill="var(--blue)"/>
      <path d="M380 300 C480 330 600 300 700 250 L700 400 L380 400 Z" fill="var(--purple)"/>
      <path d="M0 165 C130 150 260 215 360 280 C450 338 570 336 700 306 L700 400 L0 400 Z" fill="var(--pink)"/>
    </svg>

    <div class="wordmark">
      <div class="wordmark-row">
        <span class="wordmark-square"></span>
        <span class="wordmark-name">Tarts and Treats by Maren</span>
      </div>
      <span class="wordmark-rule"></span>
    </div>

    <div class="contact">
      <p class="contact-name">Tobias Lind</p>
      <p class="contact-role">CEO/Founder</p>
      <ul class="contact-list">
        <li class="contact-item">
          <svg class="contact-icon" viewBox="0 0 14 14" aria-hidden="true"><rect x="3.5" y="0.5" width="7" height="13" rx="1.5" fill="none" stroke="var(--white)" stroke-width="1.3"/><circle cx="7" cy="11" r="0.9" fill="var(--white)"/></svg>
          <span>0492 815 063</span>
        </li>
        <li class="contact-item">
          <svg class="contact-icon" viewBox="0 0 14 14" aria-hidden="true"><rect x="0.7" y="2.7" width="12.6" height="8.6" fill="none" stroke="var(--white)" stroke-width="1.3"/><path d="M1 3 L7 8 L13 3" fill="none" stroke="var(--white)" stroke-width="1.3"/></svg>
          <span>maren@tartsandtreatsbymaren.example.au</span>
        </li>
        <li class="contact-item">
          <svg class="contact-icon" viewBox="0 0 14 14" aria-hidden="true"><circle cx="7" cy="7" r="6" fill="var(--white)"/></svg>
          <span>tartsandtreatsbymaren</span>
        </li>
        <li class="contact-item">
          <svg class="contact-icon" viewBox="0 0 14 14" aria-hidden="true"><rect x="1" y="1" width="12" height="12" fill="var(--white)"/></svg>
          <span>tartsandtreatsbymaren</span>
        </li>
      </ul>
    </div>
  </section>

</body>
</html>
```